Dynamic Business Card for Sports Supplements Company

Hi! I'm looking for an awesome business card to match my existing sports supplement company. I have uploaded my current company logo and screenshot of the front page of my website.

I would like to have something dynamic and interesting and utilize the colors in the website - the reds and purples

The business card should be double sided and focus on a unique eye-catching design on the back and include all the relevant company info.

Most importantly, it should say somewhere: "Sign up on our website for a coupon code."

Target Market(s)

Mostly for women gym goers but it shouldn't be too feminine. It should be in keeping with the website design. It should flow and clearly be connected to it

Industry/Entity Type

Business

Contact Information for Business Card

Lorraine K. Vestal
CEO
LVestal@Quorvanexco.com
www.quorvanexco.com
555.417.3820
P.O. Box 47315
Linden Falls, Oregon 00000

Sign up on our website for a coupon code

Font styles to use
Serif
Sans Serif
Other font styles liked:
• Novecento font family and "Quorvanex" is in AR Destine font

Requirements
Must have
• One side should be a bold Quorvanex logo design. Even just the symbol itself may be o.k. (see attached file)

```html
<!DOCTYPE html>
<html lang="en">
<head>
<meta charset="utf-8">
<title>Quorvanex Business Card</title>
<link rel="stylesheet" href="https://fonts.googleapis.com/css2?family=Source+Sans+3:ital,wght@0,400;0,600;0,700;1,400&display=swap">
<style>
  :root {
    --backdrop: #5a4a3d;
    --card-black: #050505;
    --card-white: #ffffff;
    --brand-red: #e21e26;
    --ink: #1a1a1a;
    --light: #ffffff;
  }
  * { margin: 0; padding: 0; box-sizing: border-box; }
  html, body { width: 1200px; height: 987px; overflow: hidden; }
  body {
    background: var(--backdrop);
    font-family: "Source Sans 3", "Myriad Pro", sans-serif;
    position: relative;
  }
  .card {
    position: absolute;
    left: 293px;
    width: 614px;
    height: 351px;
    overflow: hidden;
    box-shadow: 0 2px 6px rgba(0,0,0,0.35);
  }
  .card-front { top: 130px; background: var(--card-white); }
  .card-back { top: 505px; background: var(--card-black); }

  .brand-panel {
    position: absolute;
    left: 0; top: 0;
    width: 300px; height: 100%;
    background: var(--card-black);
  }
  .brand-mark {
    position: absolute;
    left: 50%;
    transform: translateX(-50%);
    display: flex;
    flex-direction: column;
    align-items: center;
  }
  .brand-panel .brand-mark { top: 118px; }
  .brand-square {
    width: 40px; height: 40px;
    background: var(--brand-red);
    margin-bottom: 20px;
  }
  .brand-name {
    color: var(--light);
    font-weight: 700;
    letter-spacing: 1px;
    text-transform: uppercase;
    white-space: nowrap;
    line-height: 1;
  }
  .brand-panel .brand-name { font-size: 35px; }

  .accent-strip {
    position: absolute;
    right: 0; top: 0;
    width: 15px; height: 100%;
    background: var(--brand-red);
  }

  .contact {
    position: absolute;
    left: 328px;
    top: 84px;
    color: var(--ink);
    font-size: 16px;
    line-height: 1.4;
  }
  .contact-name {
    color: var(--brand-red);
    font-size: 21px;
    font-weight: 600;
    text-transform: uppercase;
    letter-spacing: 0.3px;
    line-height: 1.1;
  }
  .contact-title { margin-left: 3px; margin-bottom: 12px; }
  .contact-address { margin-left: 3px; margin-bottom: 6px; }
  .contact-list { list-style: none; margin-left: 3px; }
  .contact-list li { display: flex; align-items: center; gap: 8px; height: 23px; }
  .contact-list svg { width: 14px; height: 14px; fill: var(--brand-red); flex: none; }

  .card-back .brand-mark { top: 86px; }
  .card-back .brand-square { width: 60px; height: 60px; margin-bottom: 24px; }
  .card-back .brand-name { font-size: 56px; letter-spacing: 2px; }
  .coupon-note {
    position: absolute;
    left: 0; right: 0;
    top: 289px;
    text-align: center;
    color: var(--light);
    font-style: italic;
    font-size: 16px;
  }
</style>
</head>
<body>
  <section class="card card-front">
    <div class="brand-panel">
      <div class="brand-mark">
        <div class="brand-square"></div>
        <div class="brand-name">Quorvanex</div>
      </div>
    </div>
    <div class="contact">
      <div class="contact-name">Lorraine K. Vestal</div>
      <div class="contact-title">CEO</div>
      <div class="contact-address">P.O. Box 47315<br>Linden Falls, Oregon 00000</div>
      <ul class="contact-list">
        <li>
          <svg viewBox="0 0 16 16" aria-hidden="true"><path d="M3.6 1.2l2.3 2.6-1.2 1.8c.9 2 2.6 3.8 4.6 4.8l1.8-1.2 2.6 2.3-1.3 2.3C7.6 13.6 2.4 8.4 1.3 3.1z"/></svg>
          <span>555.417.3820</span>
        </li>
        <li>
          <svg viewBox="0 0 16 16" aria-hidden="true"><path d="M1 3h14v1.2L8 9 1 4.2z"/><path d="M1 5.8l7 4.8 7-4.8V13H1z"/></svg>
          <span>LVestal@Quorvanexco.com</span>
        </li>
        <li>
          <svg viewBox="0 0 16 16" aria-hidden="true"><circle cx="8" cy="8" r="7"/><path d="M3 6h10M3 10h10M8 1c-2.5 3-2.5 11 0 14M8 1c2.5 3 2.5 11 0 14" stroke="#fff" stroke-width="1.1" fill="none"/></svg>
          <span>www.quorvanexco.com</span>
        </li>
      </ul>
    </div>
    <div class="accent-strip"></div>
  </section>

  <section class="card card-back">
    <div class="brand-mark">
      <div class="brand-square"></div>
      <div class="brand-name">Quorvanex</div>
    </div>
    <p class="coupon-note">Sign up on our website for a coupon code</p>
  </section>
</body>
</html>
```